Modern Verdell Tree Care Website

I need a website for a full service Tree Care company. The company provides tree pruning, tree removal, tree preservation, emergency services, stump grinding, and emergency tree services.

Target Market(s)

Customers that need tree services

Industry/Entity Type

Landscaping, Tree Services

Coding

Coded - Design and coding required

Number of Pages Required

5+ page

Font styles to use
Sans Serif

Requirements
Must have
• Good clean design that showcases the services the company provides.
Nice to have
• Services page; contact form, blog, home page, about page

```html
<!DOCTYPE html>
<html lang="en">
<head>
<meta charset="utf-8">
<title>Verdell Tree Care</title>
<link href="https://fonts.googleapis.com/css2?family=Montserrat:ital,wght@0,400;0,500;0,600;0,700;1,400;1,500&display=swap" rel="stylesheet">
<style>
:root{
  --green:#8bc43f;
  --orange:#f9a533;
  --black:#000;
  --dark:#141414;
  --panel:#1b1b1b;
  --white:#fff;
  --off:#f4f6f1;
  --text-dark:#333;
  --photo-green:#5f8a30;
  --photo-deep:#3f6422;
  --photo-soil:#4a3322;
}
*{margin:0;padding:0;box-sizing:border-box}
html,body{width:1200px;height:3985px;overflow:hidden}
body{position:relative;background:var(--black);font-family:'Montserrat',sans-serif;color:var(--white)}
.abs{position:absolute}
.btn{position:absolute;display:flex;align-items:center;justify-content:center;background:var(--green);color:var(--white);border-radius:40px;font-weight:500;text-transform:uppercase;text-decoration:none}
.green{color:var(--green)}

/* header */
.site-header{left:0;top:0;width:1200px;height:165px;background:var(--black)}
.brand{display:flex;align-items:center;gap:14px}
.brand-mark{width:40px;height:40px;background:var(--green)}
.brand-name{font-weight:600;font-size:25px;letter-spacing:1px;color:var(--white);text-transform:uppercase}
.header-contact{display:flex;align-items:center;gap:14px;font-size:15px}
.icon-ring{width:34px;height:34px;border:2px solid var(--green);border-radius:50%;display:flex;align-items:center;justify-content:center}
.header-rule{left:580px;top:90px;width:510px;height:1px;background:#444}
.main-nav a{position:absolute;top:112px;font-size:15px;font-weight:500;color:var(--white);text-decoration:none}
.main-nav a.active{color:var(--green)}

/* hero */
.hero{left:0;top:165px;width:1200px;height:608px;background:linear-gradient(180deg,var(--photo-green) 0%,var(--photo-deep) 82%,var(--photo-soil) 100%)}
.hero-eyebrow{left:99px;top:405px;font-size:29px;font-weight:500}
.hero-title{left:99px;top:462px;font-size:56px;font-weight:700}
.hero-btn{left:99px;top:580px;width:229px;height:66px;font-size:25px}
.scroll-down{left:572px;top:745px;width:56px;height:56px;border-radius:50%;background:var(--white);border:3px solid var(--green);display:flex;align-items:center;justify-content:center}

/* section titles */
.section-title{left:0;width:1200px;text-align:center;font-size:38px;font-weight:600}

/* services */
.services-intro{left:236px;top:930px;width:728px;text-align:center;font-size:16px;line-height:37px}
.learn-btn{left:504px;top:1076px;width:192px;height:57px;font-size:21px}
.diamonds{left:0;top:1070px}
.svc-title{position:absolute;width:300px;text-align:center;font-size:17px;font-weight:500}
.svc-rule{position:absolute;width:34px;height:2px}
.svc-text{position:absolute;width:180px;text-align:center;font-size:16px;line-height:36px;color:var(--text-dark)}

/* about */
.about-shade{left:0;top:1790px}
.about-photo{left:700px;top:1800px;width:480px;height:530px;background:linear-gradient(180deg,#5d8a2e,#3f6422)}
.about-title{left:101px;top:1788px;font-size:38px;font-weight:600}
.about-text{left:101px;top:1860px;width:600px;font-size:16.5px;line-height:36px}
.about-quote{left:102px;top:2014px;width:600px;height:138px;border-left:3px solid var(--green);padding-left:28px;font-style:italic;font-size:16px;line-height:36px;padding-top:8px}
.read-btn{left:102px;top:2206px;width:192px;height:56px;font-size:21px}

/* blogs */
.feature-card{left:88px;top:2535px;width:557px;height:444px;border:1px solid #555}
.feature-img{left:96px;top:2543px;width:541px;height:319px;background:linear-gradient(135deg,#3b2a1d,#4f6a2a 50%,#3a2a1e)}
.feature-title{left:117px;top:2877px;font-size:17px;color:var(--green);font-weight:400}
.feature-date{left:535px;top:2892px;font-size:14px}
.feature-text{left:117px;top:2910px;width:340px;font-size:12.5px;line-height:31px}
.feature-more{left:504px;top:2928px;font-size:14px;font-weight:600;color:var(--green);text-decoration:underline;display:flex;align-items:center;gap:8px}
.post{left:659px;width:441px;height:102px;border:1px solid #555}
.post-img{position:absolute;left:7px;top:7px;width:149px;height:86px}
.post-title{position:absolute;left:179px;top:9px;font-size:12.5px;font-weight:500}
.post-date{position:absolute;left:179px;top:35px;font-size:10.5px}
.post-text{position:absolute;left:179px;top:58px;font-size:10px;white-space:nowrap}
.post-more{position:absolute;left:179px;top:81px;font-size:11px;font-weight:600;color:var(--green);text-decoration:underline}
.view-btn{left:504px;top:3041px;width:192px;height:57px;font-size:21px}

/* contact */
.footer-bg{left:0;top:3468px;width:1200px;height:517px;background:var(--dark)}
.contact-panel{left:105px;top:3193px;width:990px;height:428px;background:var(--green);border-radius:30px}
.contact-title{left:105px;top:3240px;width:990px;text-align:center;font-size:31px;font-weight:500}
.field{position:absolute;background:var(--white);border-radius:6px;color:#222;font-size:14px;font-weight:500;padding:0 16px;display:flex;align-items:center;justify-content:space-between}
.field-msg{align-items:flex-start;padding-top:16px}
.submit-btn{left:501px;top:3525px;width:198px;height:52px;font-size:20px;background:var(--white);color:var(--green)}

/* footer */
.footer-brand{left:0;top:3722px;width:1200px;justify-content:center}
.footer-nav{left:0;top:3824px;width:1200px;text-align:center;font-size:16px}
.footer-nav span{margin:0 14px}
.copyright{left:0;top:3889px;width:1200px;text-align:center;font-size:16px}
</style>
</head>
<body>

<header class="abs site-header">
  <div class="abs brand" style="left:111px;top:62px">
    <span class="brand-mark"></span>
    <span class="brand-name">Verdell Tree Care</span>
  </div>
  <div class="abs header-contact" style="left:580px;top:36px">
    <span class="icon-ring"><svg width="16" height="16" viewBox="0 0 24 24" fill="none" stroke="#8bc43f" stroke-width="2"><path d="M5 3h4l2 5-3 2a12 12 0 0 0 6 6l2-3 5 2v4a2 2 0 0 1-2 2A18 18 0 0 1 3 5a2 2 0 0 1 2-2z"/></svg></span>
    <span>+1 555 014 2290</span>
  </div>
  <div class="abs header-contact" style="left:812px;top:36px">
    <span class="icon-ring"><svg width="16" height="16" viewBox="0 0 24 24" fill="none" stroke="#8bc43f" stroke-width="2"><rect x="3" y="5" width="18" height="14" rx="1"/><path d="M3 6l9 7 9-7"/></svg></span>
    <span>HELLO@VERDELLMAIL.COM</span>
  </div>
  <div class="abs header-rule"></div>
  <nav class="main-nav">
    <a class="active" style="left:626px">HOME</a>
    <a style="left:713px">ABOUT</a>
    <a style="left:806px">SERVICES</a>
    <a style="left:912px">BLOG</a>
    <a style="left:986px">CONTACT US</a>
  </nav>
</header>

<section>
  <div class="abs hero" role="img" aria-label="Photo: hands holding soil with a young seedling, green background, soil strip below"></div>
  <div class="abs hero-eyebrow">WELCOME TO</div>
  <h1 class="abs hero-title">VERDELL TREE CARE</h1>
  <a class="btn hero-btn">Get Started</a>
  <div class="abs scroll-down"><svg width="22" height="22" viewBox="0 0 24 24" fill="none" stroke="#000" stroke-width="2.5"><path d="M6 9l6 6 6-6"/></svg></div>
</section>

<section>
  <h2 class="abs section-title" style="top:862px">OUR <span class="green">SERVICES</span></h2>
  <p class="abs services-intro">Lorem ipsum dolor sit amet, consectetur adipiscing elit, sed do eiusmod tempor incididunt ut labore et dolore magna aliqua. Ut enim ad minim veniam, quis nostrud exercitation ullamco laboris nisi ut aliquip ex ea commodo consequat.</p>
  <a class="btn learn-btn">Learn More</a>

  <svg class="abs diamonds" width="1200" height="680" viewBox="0 1070 1200 680">
    <polygon points="360,1084 567,1286 360,1480 152,1286" fill="#8bc43f"/>
    <polygon points="360,1084 556,1286 360,1494 164,1286" fill="#f4f6f1"/>
    <polygon points="840,1084 1047,1286 840,1480 632,1286" fill="#8bc43f"/>
    <polygon points="840,1084 1036,1286 840,1494 644,1286" fill="#f4f6f1"/>
    <polygon points="598,1298 806,1505 598,1700 391,1505" fill="#f9a533"/>
    <polygon points="598,1298 794,1505 598,1710 402,1505" fill="#f4f6f1"/>
    <polygon points="360,1144 406,1229 313,1229" fill="#8bc43f"/>
    <path d="M346 1212l26-28 6 5-26 27z" fill="none" stroke="#fff" stroke-width="2.5"/>
    <polygon points="840,1144 886,1229 793,1229" fill="#8bc43f"/>
    <path d="M830 1222c8-2 12-8 14-16m-2-4c-6-6-2-14 6-14 2 8-2 12-6 14z" fill="none" stroke="#fff" stroke-width="2.5"/>
    <polygon points="558,1382 638,1382 598,1462" fill="#f9a533"/>
    <g fill="none" stroke="#fff" stroke-width="2.5"><circle cx="612" cy="1414" r="14"/><path d="M612 1428v22m-10 0h26"/></g>
  </svg>

  <div class="svc-title green" style="left:210px;top:1268px">TREE PRUNING</div>
  <div class="svc-rule" style="left:343px;top:1301px;background:var(--green)"></div>
  <div class="svc-text" style="left:270px;top:1320px">Lorem ipsum dolor sit amet, consectetur adipiscing elit</div>

  <div class="svc-title green" style="left:690px;top:1268px">TREE PRESERVATION</div>
  <div class="svc-rule" style="left:823px;top:1301px;background:var(--green)"></div>
  <div class="svc-text" style="left:750px;top:1320px">Lorem ipsum dolor sit amet, consectetur adipiscing elit</div>

  <div class="svc-title" style="left:448px;top:1490px;color:var(--orange)">TREE REMOVAL</div>
  <div class="svc-rule" style="left:581px;top:1522px;background:var(--orange)"></div>
  <div class="svc-text" style="left:508px;top:1539px">Lorem ipsum dolor sit amet, consectetur adipiscing elit</div>
</section>

<section>
  <svg class="abs about-shade" width="1200" height="550" viewBox="0 1790 1200 550">
    <polygon points="0,1801 603,2339 0,2339" fill="#1b1b1b"/>
    <polygon points="541,2339 1200,1801 1200,2339" fill="#8bc43f"/>
  </svg>
  <div class="abs about-photo" role="img" aria-label="Photo: a large leafy tree"></div>
  <h2 class="abs about-title">ABOUT <span class="green">US</span></h2>
  <p class="abs about-text">Sed ut perspiciatis unde omnis iste natus error sit voluptatem accusantium doloremque laudantium, totam rem aperiam, eaque ipsa quae ab illo inventore veritatis et quasi architecto beatae vitae dicta sunt explicabo.</p>
  <blockquote class="abs about-quote">Sed ut perspiciatis unde omnis iste natus error sit voluptatem accusantium doloremque laudantium, totam rem aperiam, eaque ipsa quae ab illo inventore</blockquote>
  <a class="btn read-btn">Read More</a>
</section>

<section>
  <h2 class="abs section-title" style="top:2421px">LATEST <span class="green">BLOGS</span></h2>

  <article>
    <div class="abs feature-card"></div>
    <div class="abs feature-img" role="img" aria-label="Photo: hands planting seedlings in soil"></div>
    <h3 class="abs feature-title">LOREM IPSUM DOLOR SIT AMET</h3>
    <div class="abs feature-date">JAN 23 2024</div>
    <p class="abs feature-text">Sed ut perspiciatis unde omnis iste natus error sit voluptatem accusantium doloremque laudantium,</p>
    <a class="abs feature-more">READ MORE <svg width="18" height="10" viewBox="0 0 18 10" fill="none" stroke="#fff" stroke-width="1.5"><path d="M0 5h16M12 1l4 4-4 4"/></svg></a>
  </article>

  <article class="abs post" style="top:2535px">
    <div class="post-img" role="img" aria-label="Photo: people planting a tree" style="background:linear-gradient(135deg,#6a7a4a,#8a7a52)"></div>
    <h3 class="post-title">LOREM IPSUM DOLOR SIT AMET</h3>
    <div class="post-date">JAN 3 2024</div>
    <p class="post-text">Sed ut perspiciatis unde omnis iste natus error...</p>
    <a class="post-more">READ MORE</a>
  </article>
  <article class="abs post" style="top:2648px">
    <div class="post-img" role="img" aria-label="Photo: rows of young trees" style="background:linear-gradient(180deg,#2f7a3a,#1d5a2a)"></div>
    <h3 class="post-title">LOREM IPSUM DOLOR SIT AMET</h3>
    <div class="post-date">FEB 17 2024</div>
    <p class="post-text">Sed ut perspiciatis unde omnis iste natus error...</p>
    <a class="post-more">READ MORE</a>
  </article>
  <article class="abs post" style="top:2763px">
    <div class="post-img" role="img" aria-label="Photo: gloved hands tending a seedling" style="background:linear-gradient(135deg,#4a6a2a,#3a2a1e)"></div>
    <h3 class="post-title">LOREM IPSUM DOLOR SIT AMET</h3>
    <div class="post-date">JAN 2 2024</div>
    <p class="post-text">Sed ut perspiciatis unde omnis iste natus error...</p>
    <a class="post-more">READ MORE</a>
  </article>
  <article class="abs post" style="top:2876px">
    <div class="post-img" role="img" aria-label="Photo: planting a small sapling" style="background:linear-gradient(135deg,#6a8a42,#4a3a28)"></div>
    <h3 class="post-title">LOREM IPSUM DOLOR SIT AMET</h3>
    <div class="post-date">FEB 3 2024</div>
    <p class="post-text">Sed ut perspiciatis unde omnis iste natus error...</p>
    <a class="post-more">READ MORE</a>
  </article>

  <a class="btn view-btn">View More</a>
</section>

<div class="abs footer-bg"></div>

<section>
  <div class="abs contact-panel"></div>
  <h2 class="abs contact-title">CONTACT US</h2>
  <div class="field" style="left:122px;top:3318px;width:232px;height:52px">FIRST NAME <svg width="16" height="16" viewBox="0 0 24 24" fill="none" stroke="#8bc43f" stroke-width="2"><circle cx="12" cy="8" r="4"/><path d="M4 21c0-4 4-7 8-7s8 3 8 7"/></svg></div>
  <div class="field" style="left:363px;top:3318px;width:231px;height:52px">LAST NAME <svg width="16" height="16" viewBox="0 0 24 24" fill="none" stroke="#8bc43f" stroke-width="2"><circle cx="12" cy="8" r="4"/><path d="M4 21c0-4 4-7 8-7s8 3 8 7"/></svg></div>
  <div class="field" style="left:604px;top:3318px;width:232px;height:52px">EMAIL ADDRESS <svg width="16" height="16" viewBox="0 0 24 24" fill="none" stroke="#8bc43f" stroke-width="2"><rect x="3" y="5" width="18" height="14"/><path d="M3 6l9 7 9-7"/></svg></div>
  <div class="field" style="left:846px;top:3318px;width:232px;height:52px">PHONE NUMBER <svg width="16" height="16" viewBox="0 0 24 24" fill="none" stroke="#8bc43f" stroke-width="2"><path d="M5 3h4l2 5-3 2a12 12 0 0 0 6 6l2-3 5 2v4a2 2 0 0 1-2 2A18 18 0 0 1 3 5a2 2 0 0 1 2-2z"/></svg></div>
  <div class="field field-msg" style="left:122px;top:3381px;width:956px;height:102px">MESSAGE <svg width="18" height="18" viewBox="0 0 24 24" fill="none" stroke="#8bc43f" stroke-width="2"><path d="M3 4h18v13H8l-5 4z"/><path d="M7 9h10M7 13h6"/></svg></div>
  <a class="btn submit-btn">Submit Now</a>
</section>

<footer>
  <div class="abs brand footer-brand">
    <span class="brand-mark"></span>
    <span class="brand-name">Verdell Tree Care</span>
  </div>
  <nav class="abs footer-nav">HOME<span>|</span>ABOUT US<span>|</span>SERVICE<span>|</span>BLOG<span>|</span>CONTACT US</nav>
  <p class="abs copyright">@2024 COPYRIGHTS - ALL RIGHTS RESERVED</p>
</footer>

</body>
</html>
```